Bramblewood Card Company Business Cards

We are a trading card store with Glimmorax, sports and other TCG cards, we need a business card design that encompasses a clean cut, modern style with a retro flare. website is bramblewoodcardco.com for reference. Can utilize a comic book era feel or a more modern outdoor feel to utilize the "Pacific Northwest" elements of tress, mountains, etc.

Industry/Entity Type

Trading cards and collectibles

Contact Information for Business Card

business name, email address, phone number, name, owner job title

Font styles to use
Sans Serif

```html
<!DOCTYPE html>
<html lang="en">
<head>
<meta charset="utf-8">
<title>Bramblewood Card Company – Business Cards</title>
<link rel="stylesheet" href="https://fonts.googleapis.com/css2?family=Montserrat:wght@400;500;700;800&display=swap">
<style>
  :root {
    --backdrop-top: #d4d4d4;
    --backdrop-bottom: #a9a9a9;
    --card-grey: #757575;
    --brand-blue: #22bde0;
    --paper-white: #ffffff;
    --ink-white: #f4f4f4;
  }
  * { margin: 0; padding: 0; box-sizing: border-box; }
  html, body { width: 1200px; height: 815px; overflow: hidden; }
  body {
    position: relative;
    background: linear-gradient(160deg, var(--backdrop-top), var(--backdrop-bottom));
    font-family: "Montserrat", Arial, sans-serif;
  }
  .business-card {
    position: absolute;
    width: 520px;
    height: 297px;
    border-radius: 24px;
    background: var(--card-grey);
    overflow: hidden;
    box-shadow: 0 14px 30px rgba(0,0,0,0.28);
  }
  .card-front { left: 120px; top: 70px; }
  .card-back  { left: 560px; top: 448px; }

  .front-emblem-field { position: absolute; inset: 0; }

  .front-brand-name {
    position: absolute;
    left: 360px; top: 72px;
    width: 150px;
    color: var(--card-grey);
    font-weight: 800;
    font-size: 17px;
    line-height: 1.2;
    text-transform: uppercase;
    letter-spacing: 0.5px;
    text-align: center;
  }

  .contact-block {
    position: absolute;
    left: 30px; top: 60px;
    color: var(--ink-white);
  }
  .holder-name {
    color: var(--brand-blue);
    font-weight: 700;
    font-size: 21px;
    letter-spacing: 1.5px;
    text-transform: uppercase;
    white-space: nowrap;
  }
  .holder-title {
    font-size: 12px;
    letter-spacing: 1px;
    text-transform: uppercase;
    margin-top: 2px;
  }
  .postal-address {
    font-style: normal;
    font-size: 12.5px;
    line-height: 1.35;
    margin-top: 22px;
  }
  .contact-lines { list-style: none; margin-top: 20px; font-size: 12.5px; line-height: 1.5; }
  .contact-lines li { display: flex; align-items: center; gap: 8px; white-space: nowrap; }
  .contact-icon { width: 11px; height: 11px; flex: none; }

  .back-brand-name {
    position: absolute;
    inset: 0;
    display: flex;
    flex-direction: column;
    align-items: center;
    justify-content: center;
    gap: 2px;
    color: var(--paper-white);
    font-weight: 800;
    font-size: 30px;
    letter-spacing: 2px;
    text-transform: uppercase;
    text-align: center;
  }
  .back-brand-name .brand-sub { font-size: 18px; letter-spacing: 5px; }
</style>
</head>
<body>

  <section class="business-card card-front" aria-label="Business card front">
    <svg class="front-emblem-field" viewBox="0 0 520 297" aria-hidden="true">
      <circle cx="440" cy="100" r="160" fill="none" stroke="var(--brand-blue)" stroke-width="4"/>
      <circle cx="446" cy="94" r="156" fill="var(--paper-white)"/>
    </svg>
    <p class="front-brand-name">Bramblewood Card Company</p>

    <div class="contact-block">
      <h1 class="holder-name">Dana Whitlock</h1>
      <p class="holder-title">Manager</p>
      <address class="postal-address">418 Cedar Ridge Lane 22<br>Your County, MN 46100</address>
      <ul class="contact-lines">
        <li>
          <svg class="contact-icon" viewBox="0 0 12 12" aria-hidden="true"><path d="M2 1h3l1 3-2 1a7 7 0 0 0 3 3l1-2 3 1v3c-6 1-10-3-9-9z" fill="var(--brand-blue)"/></svg>
          (555)210-4471
        </li>
        <li>
          <svg class="contact-icon" viewBox="0 0 12 12" aria-hidden="true"><rect x="3" y="0.5" width="6" height="11" rx="1" fill="none" stroke="var(--brand-blue)" stroke-width="1.2"/></svg>
          (555)318-22904
        </li>
        <li>
          <svg class="contact-icon" viewBox="0 0 12 12" aria-hidden="true"><rect x="0.5" y="2" width="11" height="8" fill="var(--brand-blue)"/><path d="M0.5 2l5.5 4 5.5-4" fill="none" stroke="var(--card-grey)" stroke-width="1"/></svg>
          info@bramblewoodcardco.com
        </li>
        <li>
          <svg class="contact-icon" viewBox="0 0 12 12" aria-hidden="true"><circle cx="6" cy="6" r="5.4" fill="none" stroke="var(--brand-blue)" stroke-width="1.2"/><path d="M0.6 6h10.8M6 0.6c-3 3-3 7.8 0 10.8M6 0.6c3 3 3 7.8 0 10.8" fill="none" stroke="var(--brand-blue)" stroke-width="0.9"/></svg>
          www.bramblewoodcardco.com
        </li>
      </ul>
    </div>
  </section>

  <section class="business-card card-back" aria-label="Business card back">
    <p class="back-brand-name">Bramblewood<span class="brand-sub">Card Company</span></p>
  </section>

</body>
</html>
```